Popup Nightclub Grand Opening Flyer

We need to design a flyer for the grand opening of an upscale, exclusive nightclub called "Lantern". The design needs to be chic and exclusive. The background should be black and the text should primarily be white. We like minimalist designs.

Here is the text for the flyer
-
Velvetroll Atlanta Presents

Lantern (LOGO)

A Popup Nightclub Experience
For one night Only

Friday, October 18, 2013
Party begins at 9PM

INVITE ONLY

See invitation for location details
(Velvetroll Atlanta logo)

-
Examples we like

http://cdn4-x.pressfolio-example.com/sites/default/files/styles/image_content_width/hash/3b/fd/2468013579_4421_flyer.jpg?itok=K9rtQw2z

http://files.hubspace-example.net/files/8Hqq-Tr72WWE3kaRbTmcxP5QZK2F396J8nbRw4CKMHfdX2Y7qSEF-MqjxDoNrLY3QCyQJD7npjGaRq3k-Mhx6hqf3MDSWf8r3/2zenSaturdays.jpg

http://morvex-example.com/wp-content/uploads/siteskin/widgetkit/gallery/2zen/2zen-gen_qstay4-01.jpg

Hi All, one thing that we are seeing that we don't like is on over emphasis on the phrase "a popup nightclub experience" please don't make this the largest thing on the flyer

Target Market(s)

Target market is 25-35 year olds who are affluent (rich) and like luxury brands

Requirements
Must have
• Dark Background
Nice to have
• Velvetroll Logo on the bottom
Modern text that isn't curvy
Should not have
• Curved text

```html
<!DOCTYPE html>
<html lang="en">
<head>
<meta charset="utf-8">
<title>Lantern Nightclub – A Popup Nightclub Experience</title>
<link rel="stylesheet" href="https://fonts.googleapis.com/css2?family=Anton&family=Montserrat:wght@300;500;800&family=Raleway:wght@300;400;500&display=swap">
<style>
  :root {
    --ink: #000000;
    --paper: #ffffff;
    --silver: #d9d9d9;
    --steel: #9a9a9a;
    --shadow: #7a7a7a;
    --pattern-dark: #0b0b0b;
    --pattern-mid: #262626;
  }
  * { margin: 0; padding: 0; box-sizing: border-box; }
  html, body { width: 776px; height: 1200px; overflow: hidden; background: var(--ink); }
  .flyer {
    position: relative;
    width: 776px;
    height: 1200px;
    color: var(--paper);
    font-family: "Raleway", sans-serif;
    text-align: center;
    overflow: hidden;
  }
  .damask-backdrop {
    position: absolute;
    inset: 0;
    background: radial-gradient(ellipse at 50% 45%, var(--pattern-mid) 0%, var(--pattern-dark) 60%, var(--ink) 100%);
  }
  .line { position: absolute; left: 0; right: 0; white-space: nowrap; line-height: 1.2; }
  .presenter {
    top: 58px;
    font-size: 22px;
    font-weight: 400;
    letter-spacing: 0.06em;
  }
  .venue-mark {
    position: absolute;
    left: 328px;
    top: 118px;
    width: 120px;
    height: 120px;
    border-radius: 50%;
    background: var(--silver);
  }
  .venue-name {
    top: 262px;
    font-size: 70px;
    font-weight: 300;
    letter-spacing: 0.2em;
    padding-left: 0.2em;
  }
  .venue-type {
    top: 350px;
    font-size: 27px;
    font-weight: 300;
    letter-spacing: 0.1em;
  }
  .headline-block {
    position: absolute;
    top: 430px;
    left: 0; right: 0;
    display: flex;
    flex-direction: column;
    align-items: center;
    gap: 6px;
    font-weight: 400;
  }
  .headline {
    display: block;
    font-family: "Anton", sans-serif;
    text-transform: uppercase;
    line-height: 1.05;
    background: linear-gradient(180deg, var(--paper) 0%, var(--paper) 50%, var(--silver) 75%, var(--steel) 100%);
    -webkit-background-clip: text;
    background-clip: text;
    color: transparent;
  }
  .headline-top { font-size: 44px; letter-spacing: 0.02em; }
  .headline-main { font-size: 58px; letter-spacing: 0.01em; }
  .headline-bottom { font-size: 44px; letter-spacing: 0.02em; }
  .tagline {
    top: 648px;
    font-size: 28px;
    font-weight: 400;
    letter-spacing: 0.14em;
  }
  .rule {
    position: absolute;
    height: 3px;
    background: var(--paper);
  }
  .rule-upper { top: 735px; left: 100px; width: 576px; }
  .rule-lower { top: 872px; left: 130px; width: 516px; }
  .date {
    top: 756px;
    font-family: "Montserrat", sans-serif;
    font-size: 34px;
  }
  .date-day { font-weight: 300; }
  .date-rest { font-weight: 800; }
  .start-time {
    top: 818px;
    font-size: 27px;
    font-weight: 500;
  }
  .invite-ribbon {
    position: absolute;
    left: 140px;
    top: 920px;
    width: 496px;
    height: 74px;
  }
  .invite-label {
    top: 930px;
    font-family: "Montserrat", sans-serif;
    font-weight: 500;
    font-size: 36px;
    color: var(--ink);
  }
  .location-note {
    top: 1028px;
    font-size: 20px;
    font-weight: 500;
    letter-spacing: 0.17em;
  }
  .host-mark {
    position: absolute;
    top: 1070px;
    left: 0; right: 0;
    display: flex;
    justify-content: center;
    align-items: center;
    gap: 22px;
  }
  .host-dot {
    width: 62px;
    height: 62px;
    border-radius: 50%;
    background: var(--paper);
  }
  .host-name {
    text-align: left;
    font-weight: 400;
    color: var(--paper);
    line-height: 1;
  }
  .host-name-main { display: block; font-size: 44px; letter-spacing: 0.04em; }
  .host-name-city { display: block; font-size: 18px; letter-spacing: 0.12em; margin-top: 8px; }
</style>
</head>
<body>
<main class="flyer">
  <div class="damask-backdrop" role="img" aria-label="Black damask flourish pattern background"></div>

  <p class="line presenter">VELVETROLL ATLANTA PRESENTS</p>

  <div class="venue-mark" aria-hidden="true"></div>
  <h1 class="line venue-name">LANTERN</h1>
  <p class="line venue-type">NIGHTCLUB</p>

  <h2 class="headline-block">
    <span class="headline headline-top">A Popup</span>
    <span class="headline headline-main">Nightclub</span>
    <span class="headline headline-bottom">Experience</span>
  </h2>
  <p class="line tagline">FOR ONE NIGHT ONLY</p>

  <div class="rule rule-upper"></div>
  <p class="line date"><span class="date-day">FRIDAY</span><span class="date-rest">, OCTOBER 18, 2013</span></p>
  <p class="line start-time">PARTY BEGINS AT 9PM</p>
  <div class="rule rule-lower"></div>

  <svg class="invite-ribbon" viewBox="0 0 496 74" aria-hidden="true">
    <polygon points="0,22 72,22 72,66 0,66 20,44" fill="#d9d9d9"/>
    <polygon points="496,22 424,22 424,66 496,66 476,44" fill="#d9d9d9"/>
    <polygon points="60,66 76,74 76,60" fill="#7a7a7a"/>
    <polygon points="436,66 420,74 420,60" fill="#7a7a7a"/>
    <rect x="76" y="4" width="344" height="62" fill="#ffffff"/>
    <rect x="82" y="10" width="332" height="50" fill="none" stroke="#000000" stroke-width="1.5"/>
  </svg>
  <p class="line invite-label">INVITE ONLY</p>

  <p class="line location-note">SEE INVITATION FOR LOCATION DETAILS</p>

  <div class="host-mark">
    <span class="host-dot" aria-hidden="true"></span>
    <span class="host-name">
      <span class="host-name-main">VELVETROLL</span>
      <span class="host-name-city">ATLANTA</span>
    </span>
  </div>
</main>
</body>
</html>
```